Landscape design build company door flyer

I would like this flyer to convey a high-level of professionalism for a company that is excellent with communication with their clients as well as a company that does incredible installations

Went on vacation/holiday

```html
<!DOCTYPE html>
<html lang="en">
<head>
<meta charset="utf-8">
<title>Stillwater Builders – Door Hangers</title>
<link href="https://fonts.googleapis.com/css2?family=Poppins:wght@400;500;600;700;800&display=swap" rel="stylesheet">
<style>
  :root{
    --navy:#14374a;
    --navy-deep:#0f2d3d;
    --gold:#fdb515;
    --white:#ffffff;
    --page:#f2f3f4;
    --mist:#eef1f3;
  }
  *{box-sizing:border-box;margin:0;padding:0}
  html,body{width:1200px;height:1200px;overflow:hidden;background:var(--page);font-family:'Poppins',sans-serif;color:var(--navy)}
  .hanger{position:absolute;top:160px;width:340px;height:880px;background:var(--white);
    clip-path:path("M0 20 Q0 0 20 0 H320 Q340 0 340 20 V880 H0 V178 H185 Q214 178 216 128 A52 52 0 1 0 120 120 H0 Z");overflow:hidden}
  .hanger--front{left:214px}
  .hanger--back{left:647px}
  .abs{position:absolute}
  .photo{position:absolute}
  .center{text-align:center}

  /* front */
  .front-photo{left:0;top:0;width:340px;height:300px;background:linear-gradient(180deg,#b9cde0 0%,#8d7a63 35%,#5d5a55 65%,#c9c6c0 100%)}
  .brand-band{left:0;top:280px;width:340px;height:62px;background:linear-gradient(180deg,rgba(255,255,255,0),#f4f4f2 35%)}
  .brand-name{left:0;top:292px;width:340px;font-size:23px;font-weight:600;letter-spacing:.5px;color:var(--navy)}
  .brand-tag{left:0;top:319px;width:340px;font-size:11px;font-weight:500;color:var(--navy)}
  .gold-rule{left:0;top:338px;width:340px;height:3px;background:var(--gold)}
  .navy-block{left:0;top:341px;width:340px;height:218px;background:var(--navy)}
  .headline{left:0;top:348px;width:340px;font-size:35px;font-weight:800;line-height:46px;color:var(--white)}
  .ribbon{position:absolute;background:var(--gold);border-radius:30px;display:flex;align-items:center;justify-content:center;text-align:center;color:var(--navy);font-weight:500}
  .tail{position:absolute;width:0;height:0;border-top:7px solid transparent;border-bottom:7px solid transparent}
  .tail--l{border-right:18px solid var(--white)}
  .tail--r{border-left:18px solid var(--white)}
  .front-pill{left:32px;top:494px;width:276px;height:62px;font-size:14px;line-height:19px}
  .services-bg{left:0;top:559px;width:340px;height:190px;background:linear-gradient(180deg,#f3f5f6,#e9edef)}
  .section-title{left:0;top:565px;width:340px;font-size:19px;font-weight:700;display:flex;align-items:center;justify-content:center;gap:10px}
  .section-title::before,.section-title::after{content:"";width:92px;height:2px;background:var(--navy)}
  .services-list{left:8px;top:598px;width:324px;font-size:14.5px;font-weight:600;line-height:18px}
  .thumb{top:668px;width:97px;height:66px;border-radius:6px}
  .thumb--1{left:12px;background:linear-gradient(135deg,#6f6c66,#a0845c)}
  .thumb--2{left:122px;background:linear-gradient(135deg,#9fb1c0,#7f8c72)}
  .thumb--3{left:231px;background:linear-gradient(135deg,#7a5446,#4d3630)}
  .footer{left:0;top:778px;width:340px;height:102px;background:var(--navy)}
  .front-cta{left:36px;top:756px;width:268px;height:47px;font-size:13px;line-height:16px}
  .phone-pill{position:absolute;height:23px;border-radius:12px;background:var(--gold);display:flex;align-items:center;gap:3px;padding-left:4px;font-size:12px;font-weight:700;color:var(--navy)}
  .phone-ring{width:17px;height:17px;border:2px solid var(--navy);border-radius:50%;display:flex;align-items:center;justify-content:center}
  .email{position:absolute;display:flex;align-items:center;gap:5px;font-size:8.5px;color:var(--white);font-weight:500}
  .divider{position:absolute;width:1px;background:rgba(255,255,255,.45)}
  .address{position:absolute;font-size:9.5px;font-weight:700;line-height:12px;color:var(--white)}

  /* back */
  .back-photo{left:0;top:0;width:340px;height:330px;background:linear-gradient(180deg,#b98a58 0%,#8a6a4a 25%,#4f5a5d 55%,var(--navy) 100%)}
  .back-navy{left:0;top:280px;width:340px;height:110px;background:var(--navy)}
  .back-heading{left:0;top:234px;width:340px;font-size:18px;font-weight:600;line-height:23px;color:var(--white)}
  .back-pill{left:39px;top:303px;width:262px;height:84px;font-size:12.5px;font-weight:600;line-height:14.7px;padding:0 10px}
  .values-bg{left:0;top:390px;width:340px;height:372px;background:linear-gradient(180deg,#e4e9ec,var(--mist))}
  .value{position:absolute;top:418px;width:110px;text-align:center}
  .value svg{display:block;margin:0 auto 6px}
  .value span{font-size:11.5px;font-weight:700;line-height:14px;display:block}
  .reviews{left:9px;top:536px;width:322px;height:214px;border:2px solid var(--navy);border-radius:20px;background:var(--white)}
  .reviews-title{left:77px;top:524px;width:184px;height:24px;border-radius:12px;background:var(--navy);color:var(--gold);font-size:14px;font-weight:700;display:flex;align-items:center;justify-content:center}
  .stars{left:0;top:546px;width:340px;color:var(--gold);font-size:16px;letter-spacing:3px;line-height:18px}
  .quote{position:absolute;top:568px;width:146px;font-size:8.6px;line-height:10.6px;font-weight:500;text-align:center}
  .quote b{display:block;margin-top:4px;font-weight:700}
  .quote-rule{left:169px;top:572px;width:1px;height:172px;background:var(--navy)}
  .back-footer{left:0;top:762px;width:340px;height:118px;background:var(--navy);border-top:3px solid var(--gold)}
  .back-cta{left:0;top:769px;width:340px;font-size:13px;font-weight:500;line-height:16px;color:var(--gold)}
  .cta-rule{left:0;top:809px;width:340px;height:2px;background:var(--gold)}
  .back-name{left:247px;top:856px;width:90px;font-size:8px;font-weight:600;color:var(--white);text-align:center}
</style>
</head>
<body>

<!-- FRONT -->
<section class="hanger hanger--front">
  <div class="photo front-photo" role="img" aria-label="Photo of a covered backyard patio with wood beams, stone fireplace and outdoor seating"></div>
  <div class="abs brand-band"></div>
  <div class="abs brand-name center">STILLWATER BUILDERS</div>
  <div class="abs brand-tag center">OUTDOOR LIVING SPACES</div>
  <div class="abs gold-rule"></div>
  <div class="abs navy-block"></div>
  <h1 class="abs headline center">Ready to<br>Discover your<br>Zen?</h1>
  <span class="tail tail--l" style="left:14px;top:524px"></span>
  <span class="tail tail--r" style="left:308px;top:524px"></span>
  <div class="ribbon front-pill">From vision to reality, We bring<br>your dream outdoor space to life.</div>

  <div class="abs services-bg" role="img" aria-label="Faint backdrop photo of a landscaped front yard"></div>
  <h2 class="abs section-title">Services</h2>
  <p class="abs services-list center">Paver Patios • Paver Driveways • Retaining Walls • Decks &amp; Railings • Pools • Outdoor Lighting • Firepits and Fireplaces</p>
  <div class="photo thumb thumb--1" role="img" aria-label="Photo of a paver patio with built-in bench seating"></div>
  <div class="photo thumb thumb--2" role="img" aria-label="Photo of a stone retaining wall with plantings"></div>
  <div class="photo thumb thumb--3" role="img" aria-label="Photo of a wooden deck surface"></div>

  <div class="abs footer"></div>
  <div class="ribbon front-cta">Contact us today for a consultation<br>and let's bring your vision to reality.</div>
  <div class="phone-pill" style="left:16px;top:826px;width:122px">
    <span class="phone-ring"><svg width="9" height="9" viewBox="0 0 24 24"><path fill="#14374a" d="M6.6 10.8a15 15 0 0 0 6.6 6.6l2.2-2.2a1 1 0 0 1 1-.25 11.4 11.4 0 0 0 3.6.57 1 1 0 0 1 1 1V20a1 1 0 0 1-1 1A17 17 0 0 1 3 4a1 1 0 0 1 1-1h3.5a1 1 0 0 1 1 1c0 1.25.2 2.45.57 3.57a1 1 0 0 1-.25 1z"/></svg></span>(206) 555-0148
  </div>
  <div class="email" style="left:17px;top:858px">
    <svg width="11" height="8" viewBox="0 0 22 16"><rect x="1" y="1" width="20" height="14" fill="none" stroke="#fff" stroke-width="2"/><path d="M1 1l10 8 10-8" fill="none" stroke="#fff" stroke-width="2"/></svg>hello@stillwaterbuilders.com
  </div>
  <div class="divider" style="left:191px;top:820px;height:48px"></div>
  <svg class="abs" style="left:202px;top:834px" width="18" height="24" viewBox="0 0 18 24"><path d="M9 1a7.5 7.5 0 0 0-7.5 7.5C1.5 14 9 22 9 22s7.5-8 7.5-13.5A7.5 7.5 0 0 0 9 1z" fill="none" stroke="#fdb515" stroke-width="2"/><circle cx="9" cy="8.5" r="2.6" fill="none" stroke="#fdb515" stroke-width="2"/></svg>
  <p class="address" style="left:230px;top:829px">18820 NE 12th Pl,<br>Sammamish, WA<br>98074</p>
</section>

<!-- BACK -->
<section class="hanger hanger--back">
  <div class="photo back-photo" role="img" aria-label="Photo of a cedar fence above a stone retaining wall and paver patio"></div>
  <div class="abs back-navy"></div>
  <h2 class="abs back-heading center">Proudly Serving Clients in and<br>around Seattle Since 2018</h2>
  <span class="tail tail--l" style="left:14px;top:351px"></span>
  <span class="tail tail--r" style="left:308px;top:351px"></span>
  <div class="ribbon back-pill">Headquartered in Sammamish, we typically consider projects in Eastside Seattle, including the areas of Bellevue, Issaquah, Kirkland, Redmond, and Sammamish</div>

  <div class="abs values-bg" role="img" aria-label="Faint backdrop photo of a covered patio"></div>
  <div class="value" style="left:6px">
    <svg width="50" height="52" viewBox="0 0 50 52" fill="none" stroke="#14374a" stroke-width="2"><circle cx="25" cy="22" r="17"/><path d="M17 20l4-6h8l4 6-8 10z M17 20h16"/><path d="M14 36l-4 14 M36 36l2 14"/></svg>
    <span>Distinctive<br>Design</span>
  </div>
  <div class="value" style="left:111px">
    <svg width="50" height="52" viewBox="0 0 50 52" fill="none" stroke="#14374a" stroke-width="2.2"><path d="M10 8l30 36 M40 8L10 44"/><circle cx="10" cy="44" r="4"/><circle cx="40" cy="44" r="4"/><path d="M6 4l8 8 M44 4l-8 8"/></svg>
    <span>Uncompromising<br>Craftsmanship</span>
  </div>
  <div class="value" style="left:219px">
    <svg width="56" height="52" viewBox="0 0 56 52" fill="none" stroke="#14374a" stroke-width="2"><path d="M12 8l2.5 5 5.5.8-4 3.9 1 5.5-5-2.6-5 2.6 1-5.5-4-3.9 5.5-.8z M28 3l2.5 5 5.5.8-4 3.9 1 5.5-5-2.6-5 2.6 1-5.5-4-3.9 5.5-.8z M44 8l2.5 5 5.5.8-4 3.9 1 5.5-5-2.6-5 2.6 1-5.5-4-3.9 5.5-.8z"/><path d="M4 36h10l10 4h10a3 3 0 0 1 0 6H22 M14 46h20l16-10"/></svg>
    <span>Exceptional<br>Service</span>
  </div>

  <div class="abs reviews"></div>
  <h3 class="abs reviews-title">What Our Clients Say</h3>
  <div class="abs stars center">★★★★★</div>
  <p class="quote" style="left:17px">"Evan from Stillwater Builders is a magician! There is no other way to explain the transformation of our yard!!! With an incredible attention to detail and a comprehensive vision of how to transform and elevate our outdoor space I can wholeheartedly recommend hiring Stillwater Builders. Our project may not have been his biggest, but Evan gave us his undivided attention and took care of our every request"<b>- MARISOL T.</b></p>
  <div class="abs quote-rule"></div>
  <p class="quote" style="left:176px">"Evan and his team were really great to work with!! Responsive and they started right away once we gave the go. He answered all our questions and worked with us all along the way through our project. Our hard scape turned out amazing and really transformed our house and curb appeal. Our neighbors keep reaching out to get his contact so if you're on the fence about your project I would reach out sooner than later!!" our every request"<b>- DANA R.</b></p>

  <div class="abs back-footer"></div>
  <p class="abs back-cta center">Contact us today for a consultation<br>and let's bring your vision to reality.</p>
  <div class="abs cta-rule"></div>
  <div class="phone-pill" style="left:8px;top:829px;width:131px">
    <span class="phone-ring"><svg width="9" height="9" viewBox="0 0 24 24"><path fill="#14374a" d="M6.6 10.8a15 15 0 0 0 6.6 6.6l2.2-2.2a1 1 0 0 1 1-.25 11.4 11.4 0 0 0 3.6.57 1 1 0 0 1 1 1V20a1 1 0 0 1-1 1A17 17 0 0 1 3 4a1 1 0 0 1 1-1h3.5a1 1 0 0 1 1 1c0 1.25.2 2.45.57 3.57a1 1 0 0 1-.25 1z"/></svg></span>(206) 555-0148
  </div>
  <div class="email" style="left:9px;top:862px">
    <svg width="11" height="8" viewBox="0 0 22 16"><rect x="1" y="1" width="20" height="14" fill="none" stroke="#fff" stroke-width="2"/><path d="M1 1l10 8 10-8" fill="none" stroke="#fff" stroke-width="2"/></svg>hello@stillwaterbuilders.com
  </div>
  <div class="divider" style="left:144px;top:822px;height:52px"></div>
  <svg class="abs" style="left:190px;top:820px" width="12" height="15" viewBox="0 0 18 24"><path d="M9 1a7.5 7.5 0 0 0-7.5 7.5C1.5 14 9 22 9 22s7.5-8 7.5-13.5A7.5 7.5 0 0 0 9 1z" fill="none" stroke="#fdb515" stroke-width="2.4"/><circle cx="9" cy="8.5" r="2.6" fill="none" stroke="#fdb515" stroke-width="2.4"/></svg>
  <p class="address center" style="left:148px;top:841px;width:96px;font-size:8.5px;line-height:11px">18820 NE 12th Pl,<br>Sammamish, WA<br>98074</p>
  <div class="divider" style="left:245px;top:822px;height:52px"></div>
  <div class="abs back-name">STILLWATER BUILDERS</div>
</section>

</body>
</html>
```